Landscaping flier 2024

Create a 1 page flier for landscaping services
1. Must be completed in Adobe Photoshop
2. Size 8.5" x 11" (portrait layout)
3. Include logo
4. Text to include:
2024 Gravesite Landscaping Packages
info@hollowbrookmemorial.org
(201) 555-0148
hollowbrookmemorial.org
5. Use chart text for the content. DO NOT COPY THE CHART DESIGN/FORMAT. Use the chart for the text you need only.
6. Use "Pricing cards as format for laying out the chart". Open to other ideas as well.
**Use the example of chart design (handwritten) to base your design off of.
7. Photos
-include before and after care photos

```html
<!DOCTYPE html>
<html lang="en">
<head>
<meta charset="utf-8">
<title>2024 Gravesite Landscaping Packages – Hollowbrook Memorial</title>
<link href="https://fonts.googleapis.com/css2?family=Poppins:wght@300;400;500;600;700;800&display=swap" rel="stylesheet">
<style>
  :root{
    --maroon-deep:#2b0a10;
    --maroon:#4a1018;
    --maroon-mid:#7a1f2b;
    --rose:#a63a48;
    --accent:#b8323f;
    --title-dark:#3a0d14;
    --row-light:#f1f1f1;
    --row-dark:#e2e2e2;
    --tick:#2bb673;
    --cross:#8a1c2a;
    --gold:#f4b81c;
    --white:#ffffff;
    --text:#231a1c;
  }
  *{box-sizing:border-box;margin:0;padding:0}
  html,body{width:838px;height:1200px;overflow:hidden;background:#e6e6e6}
  body{font-family:"Poppins",sans-serif;color:var(--text)}
  .flier{position:relative;width:838px;height:1200px;overflow:hidden;background:var(--white)}
  .hero-photo{position:absolute;left:0;top:0;width:838px;height:490px;
    background:radial-gradient(circle at 78% 8%,rgba(240,170,80,.55),rgba(0,0,0,0) 28%),
      linear-gradient(160deg,#6b1a22 0%,#4a1218 45%,#3a1a16 75%,#4b2a1c 100%)}
  .footer-photo{position:absolute;left:0;top:907px;width:838px;height:293px;
    background:linear-gradient(180deg,#3b0d14 0%,#4a1018 50%,#3a0c12 100%)}
  .brand{position:absolute;left:0;top:66px;width:838px;display:flex;justify-content:center;align-items:center;gap:14px}
  .brand-mark{width:48px;height:48px;border-radius:50%;background:#e9e4e2}
  .brand-name{font-size:30px;font-weight:400;color:var(--white);letter-spacing:1px}
  .title{position:absolute;left:0;width:838px;text-align:center;color:var(--white);font-weight:800;line-height:1}
  .title-row1{top:164px;display:flex;justify-content:center;align-items:center;gap:12px}
  .year{background:var(--accent);border-radius:6px;font-weight:300;font-size:52px;padding:2px 14px;letter-spacing:3px;line-height:1.1}
  .title-gravesite{font-size:78px;letter-spacing:-1px}
  .title-row2{top:238px;font-size:80px;letter-spacing:-1px}
  .packages{position:absolute;top:322px;left:0;width:838px;display:flex;justify-content:center;align-items:center;gap:6px;color:var(--white)}
  .packages span{font-size:28px;letter-spacing:11px;font-weight:400}
  .packages i{display:block;width:130px;height:2px;background:var(--accent)}
  .card{position:absolute;top:406px;width:240px;height:563px;border-radius:8px;overflow:hidden;background:var(--row-light);display:flex;flex-direction:column}
  .card-seasonal{left:54px}.card-basic{left:300px}.card-perpetual{left:545px}
  .card-head{height:100px;background:#ececec;display:flex;align-items:center;justify-content:center;text-align:center;font-weight:800;font-size:20px;line-height:1.05}
  .card-seasonal .card-head,.card-perpetual .card-head{color:var(--accent)}
  .card-basic .card-head{color:var(--title-dark)}
  .card-sub{height:62px;display:flex;align-items:center;justify-content:center;text-align:center;color:var(--white);font-size:13.5px;line-height:1.2}
  .card-seasonal .card-sub{background:var(--maroon-mid)}
  .card-basic .card-sub{background:var(--rose)}
  .card-perpetual .card-sub{background:var(--maroon-deep)}
  .feature{display:flex;align-items:center;gap:7px;padding:0 10px 0 34px;font-size:12.5px;font-weight:600;line-height:1.15}
  .feature:nth-child(odd){background:var(--row-light)}
  .feature:nth-child(even){background:var(--row-dark)}
  .card-perpetual .feature-main{background:var(--row-dark)}
  .feature svg{flex:none;width:22px;height:22px}
  .feature-main{height:132px;align-items:flex-start;padding-top:18px}
  .feature-main small{display:block;font-weight:400;font-size:10.5px;margin-top:4px;line-height:1.3}
  .feature-main b{color:var(--cross);font-weight:700}
  .h51{height:51px}.h56{height:56px}.h54{height:54px}
  .badge{position:absolute;left:638px;top:370px;width:62px;height:62px;border-radius:50%;background:radial-gradient(circle,#ffd84a,var(--gold) 70%,#e39a10);display:flex;align-items:center;justify-content:center;text-align:center;font-size:10.5px;font-weight:700;line-height:1;color:var(--maroon-deep);text-transform:uppercase}
  .photo{position:absolute;top:1011px;width:241px;height:127px;border:2px solid var(--accent);border-radius:8px;background:linear-gradient(180deg,#7b8a6a 0%,#5f9a3c 40%,#4d8a2b 100%)}
  .photo-before{left:54px}.photo-after{left:300px}
  .photo-after{background:linear-gradient(180deg,#7a8a6c 0%,#5c9c3d 40%,#47862a 100%)}
  .photo-label{position:absolute;top:1130px;width:108px;height:22px;border-radius:11px;background:var(--maroon-mid);color:var(--white);font-size:11px;letter-spacing:3px;font-weight:600;display:flex;align-items:center;justify-content:center}
  .label-before{left:120px}.label-after{left:366px}
  .contact{position:absolute;left:563px;top:1006px;color:var(--white)}
  .valid{font-size:11.5px;font-weight:300}
  .phone{display:flex;align-items:center;gap:3px;font-size:27px;font-weight:600;margin-top:6px;line-height:1.2}
  .address{display:flex;gap:6px;font-size:14px;font-weight:500;line-height:1.35;margin-top:4px}
  .address svg,.phone svg{flex:none}
  .web{font-size:14.5px;font-weight:500;margin-top:8px}
  .web span{color:var(--accent);font-weight:600}
</style>
</head>
<body>
<svg width="0" height="0" style="position:absolute">
  <defs>
    <symbol id="tick" viewBox="0 0 22 22"><circle cx="11" cy="11" r="11" fill="#2bb673"/><path d="M6 11.5l3.3 3.3L16 8" fill="none" stroke="#fff" stroke-width="2.6" stroke-linecap="round" stroke-linejoin="round"/></symbol>
    <symbol id="cross" viewBox="0 0 22 22"><circle cx="11" cy="11" r="11" fill="#8a1c2a"/><path d="M7.5 7.5l7 7M14.5 7.5l-7 7" stroke="#fff" stroke-width="2.6" stroke-linecap="round"/></symbol>
  </defs>
</svg>
<main class="flier">
  <div class="hero-photo" role="img" aria-label="Cemetery path under autumn trees at dusk with a glowing street lamp"></div>
  <div class="footer-photo" role="img" aria-label="Dark cemetery grounds with red foliage"></div>

  <header class="brand">
    <span class="brand-mark"></span>
    <span class="brand-name">Hollowbrook Memorial</span>
  </header>

  <h1>
    <span class="title title-row1"><span class="year">2024</span><span class="title-gravesite">GRAVESITE</span></span>
    <span class="title title-row2">LANDSCAPING</span>
  </h1>
  <div class="packages"><i></i><span>PACKAGES</span><i></i></div>

  <section class="card card-seasonal">
    <div class="card-head">SEASONAL CARE<br>ENDOWMENT</div>
    <div class="card-sub">Seasonal<br>landscaping care</div>
    <div class="feature feature-main"><svg><use href="#tick"/></svg><div>Weeding &amp; Trimming<br>on your gravesite<small>Approximately every<br>7 weeks during the<br>growing season: <b>mid-April<br>through mid-October</b></small></div></div>
    <div class="feature h51"><svg><use href="#cross"/></svg>Monument Leveling</div>
    <div class="feature h56"><svg><use href="#cross"/></svg>Payment ensures grave<br>care forever</div>
    <div class="feature h54"><svg><use href="#cross"/></svg>Full bed of boxwood<br>shrubs</div>
    <div class="feature h56"><svg><use href="#cross"/></svg>Replace of shrubs</div>
    <div class="feature h51"><svg><use href="#cross"/></svg>Trust certificate</div>
  </section>

  <section class="card card-basic">
    <div class="card-head">BASIC CARE<br>ENDOWMENT</div>
    <div class="card-sub">Landscaping forever<br>for graves with no plantings</div>
    <div class="feature feature-main"><svg><use href="#tick"/></svg><div>Weeding &amp; Trimming<br>on your gravesite<small>2 times per year:<br><b>mid-May &amp;<br>mid-September</b></small></div></div>
    <div class="feature h51"><svg><use href="#tick"/></svg>Monument Leveling</div>
    <div class="feature h56"><svg><use href="#tick"/></svg>Payment ensures grave<br>care forever</div>
    <div class="feature h54"><svg><use href="#cross"/></svg>Full bed of boxwood<br>shrubs</div>
    <div class="feature h56"><svg><use href="#cross"/></svg>Replace of shrubs</div>
    <div class="feature h51"><svg><use href="#cross"/></svg>Trust certificate</div>
  </section>

  <section class="card card-perpetual">
    <div class="card-head">PERPETUAL CARE<br>ENDOWMENT</div>
    <div class="card-sub">Landscaping forever<br>for graves with plantings</div>
    <div class="feature feature-main"><svg><use href="#tick"/></svg><div>Weeding &amp; Trimming<br>on your gravesite<small>Approximately every 7<br>weeks during the growing<br>season: <b>mid-April through<br>mid-October</b></small></div></div>
    <div class="feature h51"><svg><use href="#tick"/></svg>Monument Leveling</div>
    <div class="feature h56"><svg><use href="#tick"/></svg>Payment ensures grave<br>care forever</div>
    <div class="feature h54"><svg><use href="#tick"/></svg>Full bed of boxwood<br>shrubs</div>
    <div class="feature h56"><svg><use href="#tick"/></svg>Replace of shrubs</div>
    <div class="feature h51"><svg><use href="#tick"/></svg>Trust certificate</div>
  </section>

  <div class="badge">Most<br>Popular</div>

  <div class="photo photo-before" role="img" aria-label="Before: overgrown gravesite with untrimmed shrubs"></div>
  <div class="photo photo-after" role="img" aria-label="After: neatly trimmed boxwood shrub at a gravesite"></div>
  <div class="photo-label label-before">BEFORE</div>
  <div class="photo-label label-after">AFTER</div>

  <footer class="contact">
    <div class="valid">Valid through 10.31.2024</div>
    <div class="phone"><svg width="18" height="18" viewBox="0 0 24 24"><path d="M6.6 10.8a15 15 0 0 0 6.6 6.6l2.2-2.2a1 1 0 0 1 1-.25 11.4 11.4 0 0 0 3.6.57 1 1 0 0 1 1 1V20a1 1 0 0 1-1 1A17 17 0 0 1 3 4a1 1 0 0 1 1-1h3.5a1 1 0 0 1 1 1c0 1.25.2 2.45.57 3.57a1 1 0 0 1-.25 1z" fill="#b8323f"/></svg>(201) 555-0148</div>
    <div class="address"><svg width="14" height="18" viewBox="0 0 14 18"><path d="M7 0a7 7 0 0 0-7 7c0 5 7 11 7 11s7-6 7-11a7 7 0 0 0-7-7zm0 9.5A2.5 2.5 0 1 1 7 4.5a2.5 2.5 0 0 1 0 5z" fill="#b8323f"/></svg><div>48 Alder Lane<br>Fairmont Glen, NJ 07999</div></div>
    <div class="web">www.<span>hollowbrookmemorial</span>.org</div>
  </footer>
</main>
</body>
</html>
```